Stage Design Company Business Card

We are looking to step up up our business card design for our team.

We are a Full service Design and Consultation company for Stage and TV with an emphasis in Theatrical Lighting.

We like our materials to be clean and modern with solid colors free of patterns and gradients. Our brand consists of 4 primary colors Purple, Black, Grey, and White. Provided is our Word Mark as well as our Symbol Logo.

We would like our cards to leave an impression beyond the information, show our attention to design and detail, and make our marks an easily recognized feature (together or apart) for our clients.

We need a warm approachable comfortable feel for some clients, and a professional flair for the board member type clients.

Attached are our brand elements, and our existing cards to give a sense of our style and a glipse at the information we provide on our cards.

Target Market(s)

broad client base from church leaders to high school teachers and architects.

Industry/Entity Type

Business

Contact Information for Business Card

We format our phone number with periods not parenthesis or dashes. Information will be edited for each of our team members, and team member specific cards are not part of this scope, but rather a template so to speak.

Font styles to use
Sans Serif

Colors
6b449b
ffffff
000000
333333
aaaaaa

Requirements
Must have
• Wordmark and logo mark present (does not need to exist on the same side of card)
• Brand Colors,
• Name, Phone, Email, Address.
• Unique choices that make someone stop and take a second look
Nice to have
• It would be nice to somehow convey what we DO, as our brand name does not lend itself to this, outside of an obvious tagline though.....
• social media if not crowded. all of our handles match (instagram, twitter, facebook)
Should not have
• "clipart"

```html
<!DOCTYPE html>
<html lang="en">
<head>
<meta charset="utf-8">
<title>Orvane Business Card</title>
<link href="https://fonts.googleapis.com/css2?family=Open+Sans:wght@400;600&display=swap" rel="stylesheet">
<style>
  :root {
    --backdrop: #2b2b2b;
    --card: #0e0e0e;
    --ink: #f2f2ee;
    --ink-soft: #d6d6d2;
    --brand-purple: #6b449b;
    --divider: #333333;
  }
  * { box-sizing: border-box; margin: 0; padding: 0; }
  html, body {
    width: 1200px; height: 899px; overflow: hidden;
    background: var(--backdrop);
    font-family: "Open Sans", sans-serif;
  }
  .canvas {
    position: relative; width: 1200px; height: 899px;
    display: flex; align-items: center; justify-content: center; gap: 40px;
  }
  .card {
    position: relative; width: 520px; height: 300px;
    background: var(--card); border-radius: 24px; color: var(--ink);
    overflow: hidden;
  }
  .card-front { display: flex; }
  .mark-panel {
    width: 44%; height: 100%;
    display: flex; align-items: center; justify-content: center; gap: 10px;
    border-right: 1px solid var(--divider);
  }
  .brand-dot {
    width: 14px; height: 14px; border-radius: 50%; background: var(--brand-purple);
  }
  .brand-name {
    font-weight: 600; font-size: 26px; letter-spacing: 4px; color: var(--ink);
  }
  .contact-panel {
    flex: 1; padding: 58px 0 0 34px; color: var(--ink-soft);
  }
  .person-name { font-size: 23px; font-weight: 400; color: var(--ink); line-height: 1.1; }
  .person-role { font-size: 12.5px; margin-top: 3px; color: var(--brand-purple); font-weight: 600; }
  .address { font-size: 13px; line-height: 1.35; margin-top: 14px; }
  .contact-list { list-style: none; margin-top: 10px; font-size: 13px; }
  .contact-list li { display: flex; align-items: center; gap: 9px; line-height: 1.45; }
  .contact-list svg { width: 11px; height: 11px; fill: var(--brand-purple); flex: none; }
  .card-back {
    display: flex; flex-direction: column; align-items: center; justify-content: center; gap: 30px;
  }
  .card-back .brand-dot { width: 22px; height: 22px; }
  .card-back .brand-name { font-size: 24px; letter-spacing: 16px; margin-right: -16px; }
  .edge-line {
    position: absolute; left: 0; right: 0; bottom: 0; height: 4px; background: var(--brand-purple);
  }
</style>
</head>
<body>
<main class="canvas">
  <section class="card card-front">
    <div class="mark-panel">
      <span class="brand-dot"></span>
      <span class="brand-name">ORVANE</span>
    </div>
    <div class="contact-panel">
      <h1 class="person-name">Elliot Marsh</h1>
      <p class="person-role">Lighting Director</p>
      <p class="address">48 Proscenium Way<br>Stageford, 204518.</p>
      <ul class="contact-list">
        <li><svg viewBox="0 0 24 24"><path d="M6.6 10.8a15.1 15.1 0 0 0 6.6 6.6l2.2-2.2c.3-.3.7-.4 1-.2 1.1.4 2.300.6 3.6.6.6 0 1 .4 1 1V20c0 .6-.4 1-1 1A17 17 0 0 1 3 4c0-.6.4-1 1-1h3.5c.6 0 1 .4 1 1 0 1.3.2 2.5.6 3.6.1.3 0 .7-.2 1z"/></svg>044.218.730.415</li>
        <li><svg viewBox="0 0 24 24"><path d="M2 5h20v14H2zm2 2v.5l8 5 8-5V7l-8 5z"/></svg>hello@orvane.com</li>
        <li><svg viewBox="0 0 24 24"><path d="M10.6 13.4a1 1 0 0 1 0-1.4l3.5-3.5a1 1 0 1 1 1.4 1.4L12 13.4a1 1 0 0 1-1.4 0zM8.5 20a4.5 4.5 0 0 1-3.2-7.7l2.5-2.5 1.4 1.4-2.5 2.5a2.5 2.5 0 0 0 3.5 3.5l2.5-2.5 1.4 1.4-2.5 2.5A4.5 4.5 0 0 1 8.5 20zm7.7-5.8-1.4-1.4 2.5-2.5a2.5 2.5 0 0 0-3.5-3.5l-2.5 2.5-1.4-1.4 2.5-2.5a4.5 4.5 0 0 1 6.4 6.4z"/></svg>www.orvane.com</li>
      </ul>
    </div>
    <span class="edge-line"></span>
  </section>
  <section class="card card-back">
    <span class="brand-dot"></span>
    <span class="brand-name">ORVANE</span>
    <span class="edge-line"></span>
  </section>
</main>
</body>
</html>
```